Specialised investor in e-mobility and energy wants business card design

We need a business card design that fits our existing corporate design. <The look and feel must be 'sharp'/'clean', dynamic, communicate momentum, professionalism etc (as one would imagine from a firm in the financial sector). We like the idea of a reverse-side of the card that includes the logo, and the name and contact details on the other. We expect the deliverable to be whatever format might be required to be able to get cards printed directly by a service such as kelmo press. Our website is www.zub.capital

```html
<!DOCTYPE html>
<html lang="en">
<head>
<meta charset="utf-8">
<title>Zub Capital – Business Card</title>
<link rel="stylesheet" href="https://fonts.googleapis.com/css2?family=Montserrat:wght@400;500;700&display=swap">
<style>
  :root {
    --backdrop: #7a5a3e;
    --card: #ffffff;
    --green-dark: #2f5322;
    --green-light: #7cb342;
    --ink: #1f1f1f;
  }
  * { margin: 0; padding: 0; box-sizing: border-box; }
  html, body { width: 900px; height: 1200px; overflow: hidden; }
  body {
    background: var(--backdrop);
    font-family: "Montserrat", Arial, sans-serif;
    position: relative;
  }
  .card {
    position: absolute;
    left: 80px;
    width: 742px;
    height: 440px;
    background: var(--card);
    border-radius: 36px;
    box-shadow: 0 6px 14px rgba(0,0,0,0.45);
  }
  .card--front { top: 132px; }
  .card--back { top: 638px; }

  .brand-name {
    position: absolute;
    color: var(--green-dark);
    font-weight: 500;
    white-space: nowrap;
    letter-spacing: 0.5px;
  }
  .card--front .brand-name { left: 22px; top: 68px; font-size: 56px; }
  .card--back .brand-name { left: 0; right: 0; top: 188px; text-align: center; font-size: 66px; }

  .holder { position: absolute; left: 37px; top: 268px; }
  .holder-name { font-size: 26px; font-weight: 700; color: var(--green-dark); line-height: 1.1; }
  .holder-role { font-size: 16px; color: var(--ink); margin-top: 2px; }

  .divider {
    position: absolute;
    left: 40px; top: 331px;
    width: 666px; height: 2px;
    background: var(--green-light);
  }

  .contact-list { position: absolute; left: 36px; top: 352px; list-style: none; }
  .contact-item {
    display: flex; align-items: center;
    font-size: 16px; color: var(--ink);
    height: 22px;
  }
  .contact-item svg { width: 14px; height: 14px; margin-right: 12px; fill: var(--green-light); }

  .address {
    position: absolute; left: 470px; top: 378px;
    font-size: 16px; color: var(--ink); line-height: 20px;
    font-style: normal;
  }
</style>
</head>
<body>
  <section class="card card--front">
    <div class="brand-name">Zub Capital</div>

    <div class="holder">
      <div class="holder-name">Mark Delaney</div>
      <div class="holder-role">Owner</div>
    </div>

    <div class="divider"></div>

    <ul class="contact-list">
      <li class="contact-item">
        <svg viewBox="0 0 14 14" aria-hidden="true"><path d="M1 5c0-2 3-3 6-3s6 1 6 3v1h-3V5H4v1H1z"/><rect x="3" y="7" width="8" height="5" rx="1"/></svg>
        +41 70418 2257
      </li>
      <li class="contact-item">
        <svg viewBox="0 0 14 14" aria-hidden="true"><path d="M1 3h12v1L7 8 1 4z"/><path d="M1 5.5l6 4 6-4V11H1z"/></svg>
        mark@zub.capital
      </li>
      <li class="contact-item">
        <svg viewBox="0 0 14 14" aria-hidden="true"><circle cx="7" cy="7" r="6"/></svg>
        www.zub.capital.com
      </li>
    </ul>

    <address class="address">48 Harbor Lane, Suite 210<br>Brenton, PA 19020</address>
  </section>

  <section class="card card--back">
    <div class="brand-name">Zub Capital</div>
  </section>
</body>
</html>
```